Brightbay Orthodontics business card design

Need a business card design that reflects our re-branding (orthodontic office - braces) and a new partnership with a pediatric dental office. We would like to include "for adults and children" on the card as well so adults know they are welcome to get their braces here as well. Office design is modern and would like business card to reflect a modern type look. Here's the text we would like to be included on the card:

Darren Wolcott, DDS, MSD
5214 West Linden Avenue, Suite 204
Mansfield, TX 76991
555-418-2637
www.brightbayortho.example
info@brightbayortho.example

Can we add the following to the existing designs? Darren Wolcott, DDS, MSD 5214 West Linden Avenue, Suite 204 Mansfield, TX 76991 555-418-2637

Does anyone have any more vertical designs available? Thanks!

Dental

```html
<!DOCTYPE html>
<html lang="en">
<head>
<meta charset="utf-8">
<title>Brightbay Orthodontics – Business Card</title>
<link rel="stylesheet" href="https://fonts.googleapis.com/css2?family=Fredoka:wght@600&family=Open+Sans:wght@400;600;700&display=swap">
<style>
  :root {
    --stage: #d9d9d6;
    --card-white: #ffffff;
    --card-grey: #c9c9c9;
    --ink: #1c1c1c;
    --text: #333333;
    --magenta: #d0007a;
    --black-band: #151515;
    --yellow: #ffe600;
    --blue: #1f7fc4;
    --green: #7dc242;
    --orange: #f7941d;
    --name-blue: #2a7bbf;
    --icon-green: #3aa84a;
  }
  * { box-sizing: border-box; margin: 0; padding: 0; }
  html, body { width: 1200px; height: 871px; overflow: hidden; }
  body { background: var(--stage); position: relative; font-family: "Open Sans", sans-serif; }

  .card {
    position: absolute;
    width: 560px;
    height: 320px;
    overflow: hidden;
    box-shadow: 0 10px 24px rgba(0,0,0,0.25);
  }

  /* Front */
  .card-front {
    left: 60px; top: 90px;
    background: linear-gradient(180deg, #f4f4f4 0%, #e6e6e6 55%, var(--card-grey) 100%);
  }
  .brand { display: flex; align-items: center; gap: 14px; }
  .brand-dot { border-radius: 50%; background: var(--ink); flex: none; }
  .brand-name {
    font-family: "Fredoka", sans-serif; font-weight: 600; color: var(--ink);
    line-height: 0.95;
  }
  .card-front .brand { position: absolute; left: 118px; top: 62px; }
  .card-front .brand-dot { width: 26px; height: 26px; }
  .card-front .brand-name { font-size: 44px; }

  .audience-band {
    position: absolute; left: 0; right: 0; top: 210px; height: 40px;
    display: flex;
  }
  .audience-band span {
    display: flex; align-items: center; justify-content: center;
    color: #fff; font-size: 17px; letter-spacing: 1.5px; text-transform: uppercase;
  }
  .band-children { background: var(--magenta); width: 52%; }
  .band-adults { background: var(--black-band); flex: 1; }

  /* Back */
  .card-back { left: 580px; top: 470px; background: var(--card-white); }
  .colour-strip {
    position: absolute; left: 0; top: 0; bottom: 0; width: 22px;
    display: flex; flex-direction: column;
  }
  .colour-strip i { flex: 1; display: block; }
  .strip-yellow { background: var(--yellow); }
  .strip-blue { background: var(--blue); }
  .strip-magenta { background: var(--magenta); }
  .strip-green { background: var(--green); }
  .strip-orange { background: var(--orange); }

  .card-back .brand { position: absolute; left: 52px; top: 38px; gap: 10px; }
  .card-back .brand-dot { width: 16px; height: 16px; }
  .card-back .brand-name { font-size: 27px; }

  .postal {
    position: absolute; left: 62px; top: 138px;
    font-size: 12px; line-height: 18px; color: var(--text); font-style: normal;
  }
  .contact-list {
    position: absolute; left: 52px; top: 190px; list-style: none;
    font-size: 12.5px; color: var(--text);
  }
  .contact-list li { display: flex; align-items: center; gap: 10px; height: 22px; }
  .contact-list svg { width: 13px; height: 13px; flex: none; }

  .person { position: absolute; right: 46px; top: 176px; text-align: right; }
  .person-name { font-weight: 700; font-size: 18px; color: var(--name-blue); letter-spacing: 0.5px; }
  .person-role { font-size: 12px; color: var(--text); margin-top: 2px; }
</style>
</head>
<body>

<section class="card card-front" aria-label="Card front">
  <div class="brand">
    <span class="brand-dot"></span>
    <span class="brand-name">Brightbay<br>Orthodontics</span>
  </div>
  <div class="audience-band">
    <span class="band-children">For Children</span>
    <span class="band-adults">And Adults</span>
  </div>
</section>

<section class="card card-back" aria-label="Card back">
  <div class="colour-strip">
    <i class="strip-yellow"></i><i class="strip-blue"></i><i class="strip-magenta"></i><i class="strip-green"></i><i class="strip-orange"></i>
  </div>

  <div class="brand">
    <span class="brand-dot"></span>
    <span class="brand-name">Brightbay<br>Orthodontics</span>
  </div>

  <address class="postal">
    5214 West Linden Avenue, Suite 204<br>Mansfield, TX 76991
  </address>

  <ul class="contact-list">
    <li>
      <svg viewBox="0 0 16 16" aria-hidden="true"><path d="M2 6c0-2 2-3 6-3s6 1 6 3v1h-3V5.5H5V7H2z M4 8h8l1 5H3z" fill="var(--icon-green)"/></svg>
      555-418-2637
    </li>
    <li>
      <svg viewBox="0 0 16 16" aria-hidden="true"><rect x="1.5" y="3.5" width="13" height="9" fill="none" stroke="var(--icon-green)" stroke-width="1.5"/><path d="M1.5 3.5 8 9l6.5-5.5" fill="none" stroke="var(--icon-green)" stroke-width="1.5"/></svg>
      info@brightbayortho.example
    </li>
    <li>
      <svg viewBox="0 0 16 16" aria-hidden="true"><circle cx="8" cy="8" r="6.5" fill="none" stroke="var(--icon-green)" stroke-width="1.5"/><path d="M1.5 8h13M8 1.5c-3 3.5-3 9.5 0 13M8 1.5c3 3.5 3 9.5 0 13" fill="none" stroke="var(--icon-green)" stroke-width="1.2"/></svg>
      www.brightbayortho.example
    </li>
  </ul>

  <div class="person">
    <div class="person-name">Darren Wolcott</div>
    <div class="person-role">DDS, MSD</div>
  </div>
</section>

</body>
</html>
```